Northfield Builders Guild Business card

We are looking for a new business card design with photo included.
Our business is a nonprofit construction contractor membership organization. We offer business education, assist with business setup and licensing, provide safety training, and provide a member directory.
URL: www.builderslinkguild.org
Color code:
CMYK: 0 cyan, 42 magenta, 100 yellow, 0 black for Print.
Hexidecimal: #FF9900
RGB: R 255; G 153; B 0

```html
<!DOCTYPE html>
<html lang="en">
<head>
<meta charset="utf-8">
<title>Northfield Builders Guild – Business Card</title>
<link href="https://fonts.googleapis.com/css2?family=Arimo:wght@400;700&display=swap" rel="stylesheet">
<style>
  :root {
    --bg: #6a6a6a;
    --card: #1e1d1c;
    --orange: #f7941d;
    --white: #ffffff;
    --rule: #4a4948;
  }
  * { margin: 0; padding: 0; box-sizing: border-box; }
  html, body {
    width: 1093px;
    height: 1200px;
    overflow: hidden;
    background: var(--bg);
    font-family: "Arimo", Arial, sans-serif;
  }
  .card {
    position: absolute;
    left: 265px;
    width: 578px;
    height: 357px;
    background: var(--card);
    color: var(--white);
    text-align: center;
  }
  .card--front { top: 226px; }
  .card--back  { top: 620px; }

  .contact { padding-top: 58px; }
  .contact__name {
    color: var(--orange);
    font-weight: 700;
    font-size: 22px;
    line-height: 24px;
    letter-spacing: 0.2px;
  }
  .contact__title {
    font-size: 15px;
    line-height: 18px;
  }
  .rule {
    width: 111px;
    height: 1px;
    background: var(--rule);
    margin: 10px auto 11px;
  }
  .contact__line {
    font-size: 16.5px;
    line-height: 22px;
  }
  .label { color: var(--orange); font-weight: 700; }
  .org__name {
    color: var(--orange);
    font-weight: 700;
    font-size: 17px;
    line-height: 22px;
  }
  .org__address {
    font-size: 16.5px;
    line-height: 21px;
  }

  .wordmark {
    position: absolute;
    top: 118px;
    left: 0;
    right: 0;
    color: var(--white);
    font-weight: 700;
    text-transform: uppercase;
  }
  .wordmark__top {
    display: block;
    font-size: 54px;
    line-height: 56px;
    letter-spacing: 1px;
  }
  .wordmark__bottom {
    display: block;
    font-size: 33px;
    line-height: 40px;
    letter-spacing: 3px;
  }
  .website {
    position: absolute;
    top: 298px;
    left: 0;
    right: 0;
    font-size: 16.5px;
  }
  .website__domain { color: var(--orange); }
</style>
</head>
<body>
  <section class="card card--front" aria-label="Business card front">
    <div class="contact">
      <h1 class="contact__name">DANIEL WHITFORD</h1>
      <p class="contact__title">MANAGING DIRECTOR</p>
      <div class="rule"></div>
      <p class="contact__line"><span class="label">Office:</span> (555) 214-3087</p>
      <p class="contact__line"><span class="label">Phone:</span> 800-555-0147</p>
      <p class="contact__line"><span class="label">Fax:</span> 555.619.0342</p>
      <p class="contact__line"><span class="label">Email:</span> support@nbguild.org</p>
      <div class="rule"></div>
      <p class="org__name">Northfield Builders Guild</p>
      <p class="org__address">2450 Cedar Ridge Rd.,<br>Suite #210, Fairview, OR 97024</p>
    </div>
  </section>

  <section class="card card--back" aria-label="Business card back">
    <div class="wordmark">
      <span class="wordmark__top">Northfield</span>
      <span class="wordmark__bottom">Builders Guild</span>
    </div>
    <p class="website">www.<span class="website__domain">builderslinkguild</span>.org</p>
  </section>
</body>
</html>
```